New business card/stationary for a consulting company

I am looking for a clean and very professional looking business card for my consulting company as well as corresponding stationary. I am uploading our logo. I like simple and powerful for the feel. No graphics but I am open on everything else. Below is my contact information but would like the final to be in a version I can add my employees information into and print. Thank you.

Daniel Whitcombe
dan@ferncliffadvisory.com
2870 North 9th Avenue, Summit Floor, Elm Ridge, Illinois 60531
www.ferncliffadvisory.com

Industry/Entity Type

Consulting

Contact Information for Business Card

Daniel Whitcombe
dan@ferncliffadvisory.com
www.ferncliffadvisory.com

Font styles to use
Serif
Sans Serif

Requirements
Must have
• Our logo and the business card details.
Nice to have
• our website www.ferncliffadvisory.com

```html
<!DOCTYPE html>
<html lang="en">
<head>
<meta charset="utf-8">
<title>Ferncliff Advisory — Business Card</title>
<link rel="stylesheet" href="https://fonts.googleapis.com/css2?family=Open+Sans:wght@300;400;700&display=swap">
<style>
  :root {
    --backdrop: #2e2926;
    --card: #151515;
    --card-edge: #222;
    --ink: #f2f2f2;
    --ink-soft: #b9b9b9;
    --rule: #8a8a8a;
  }
  * { box-sizing: border-box; margin: 0; padding: 0; }
  html, body { width: 1200px; height: 864px; overflow: hidden; }
  body {
    background: var(--backdrop);
    font-family: "Open Sans", Arial, sans-serif;
    color: var(--ink);
    display: flex;
    align-items: center;
    justify-content: center;
    gap: 40px;
  }
  .card {
    width: 560px;
    height: 320px;
    background: var(--card);
    border: 1px solid var(--card-edge);
    border-radius: 3px;
    box-shadow: 0 10px 30px rgba(0,0,0,.45);
    position: relative;
  }
  /* front */
  .card-front {
    display: flex;
    flex-direction: column;
    align-items: center;
    justify-content: center;
    gap: 30px;
  }
  .brand {
    display: flex;
    align-items: center;
    gap: 12px;
    font-weight: 300;
    letter-spacing: .12em;
    text-transform: uppercase;
    color: var(--ink);
  }
  .brand-square { width: 14px; height: 14px; background: var(--ink); }
  .card-front .brand { font-size: 26px; }
  .card-front .brand-square { width: 20px; height: 20px; }
  .front-web {
    font-size: 12px;
    letter-spacing: .42em;
    color: var(--ink-soft);
    font-weight: 300;
  }
  /* back */
  .card-back {
    display: flex;
    align-items: center;
  }
  .back-brand {
    width: 270px;
    display: flex;
    justify-content: center;
  }
  .back-brand .brand { font-size: 15px; }
  .divider {
    width: 1px;
    height: 170px;
    background: linear-gradient(to bottom, transparent, var(--rule) 20%, var(--rule) 80%, transparent);
  }
  .contact {
    padding-left: 28px;
    font-size: 13px;
    line-height: 1.45;
  }
  .contact-name {
    font-weight: 700;
    font-size: 17px;
    text-transform: uppercase;
    letter-spacing: .02em;
    margin-bottom: 10px;
  }
  .contact-line { display: flex; align-items: center; gap: 8px; }
  .contact-line svg { width: 11px; height: 11px; flex: none; }
</style>
</head>
<body>
  <section class="card card-front">
    <div class="brand"><span class="brand-square"></span>Ferncliff Advisory</div>
    <p class="front-web">www.ferncliffadvisory.com</p>
  </section>

  <section class="card card-back">
    <div class="back-brand">
      <div class="brand"><span class="brand-square"></span>Ferncliff Advisory</div>
    </div>
    <div class="divider"></div>
    <div class="contact">
      <p class="contact-name">Daniel Whitcombe</p>
      <p>2870 North 9th Avenue</p>
      <p>Summit Floor, Elm Ridge</p>
      <p>Illinois 60531</p>
      <p class="contact-line">
        <svg viewBox="0 0 12 12" aria-hidden="true"><rect x="0.5" y="2" width="11" height="8" rx="1" fill="#f2f2f2"/><path d="M1 2.5 6 6.5 11 2.5" fill="none" stroke="#151515" stroke-width="1.2"/></svg>
        dan@ferncliffadvisory.com
      </p>
      <p class="contact-line">
        <svg viewBox="0 0 12 12" aria-hidden="true"><circle cx="6" cy="6" r="5.2" fill="none" stroke="#f2f2f2" stroke-width="1.2"/><ellipse cx="6" cy="6" rx="2.2" ry="5.2" fill="none" stroke="#f2f2f2" stroke-width="1"/><path d="M1 6h10" stroke="#f2f2f2" stroke-width="1"/></svg>
        www.ferncliffadvisory.com
      </p>
    </div>
  </section>
</body>
</html>
```